Business Cards Design for the electrical wholesaler: clean bold dynamic :)

We need a business card design that would follow our latest brand guidelines. As an electrical wholesaler we want to bring a fresh look and feel into the industry. The design should be clean bold and dynamic. It should come alive with the renewed energy of our green colour. Our grey colour should keep things balanced and complement the notion of maturity and responsibility. We employ Lato as a corporate font however are not bound by this font and we’re open to interpretation here.

Target Market(s)

Electrical contractors

Industry/Entity Type

Business

Contact Information for Business Card

Logo
Name & Surname: Halyna Dorosh
Job Title: Director of Marketing
Email: halya.dorosh@quillmail.example
Cell phone: XXX.XXX.XXXX
Address: 20517 - 87 Ave. Edmonton, AB, Canada. T6K 4N8
Business Phone: 780.555.0184
Website: www.brovix.example

Font styles to use
Other font styles liked:
• Lato

Requirements
Must have
• Logo & website
Nice to have
• Brand elements - some of them you may find in the attached Brand Guidelines (e.g. three lines on the background signifying "W")

```html
<!DOCTYPE html>
<html lang="en">
<head>
<meta charset="utf-8">
<title>Brovix Business Cards</title>
<link href="https://fonts.googleapis.com/css2?family=Montserrat:wght@400;500;600&display=swap" rel="stylesheet">
<style>
  :root {
    --stage: #2b2b2b;
    --card-dark: #1f1f1f;
    --card-light: #ffffff;
    --green: #8cc63f;
    --grey: #4a4b4d;
    --grey-mid: #5e5f61;
    --text-light: #e6e6e6;
  }
  * { box-sizing: border-box; margin: 0; padding: 0; }
  html, body { width: 1200px; height: 738px; overflow: hidden; }
  body {
    background: var(--stage);
    font-family: "Montserrat", sans-serif;
    display: flex;
    align-items: center;
    justify-content: center;
    gap: 50px;
  }
  .card {
    position: relative;
    width: 500px;
    height: 286px;
    border-radius: 3px;
    overflow: hidden;
    box-shadow: 0 10px 30px rgba(0,0,0,.45);
  }

  /* back side */
  .card--back { background: var(--card-dark); }
  .card--back .brand {
    position: absolute;
    top: 100px; left: 0; right: 0;
    display: flex; align-items: center; justify-content: center; gap: 14px;
  }
  .brand__dot {
    width: 30px; height: 30px; background: var(--green); border-radius: 50%;
  }
  .brand__name {
    font-size: 54px; font-weight: 500; letter-spacing: 1px; line-height: 1;
  }
  .card--back .brand__name { color: var(--text-light); }
  .card--back .site {
    position: absolute; bottom: 26px; left: 0; right: 0;
    text-align: center; font-size: 12px; letter-spacing: 1.5px; color: var(--text-light);
  }
  .site .accent { color: var(--green); }

  /* front side */
  .card--front { background: var(--card-light); }
  .card--front .brand {
    position: absolute; top: 40px; left: 36px;
    display: flex; align-items: center; gap: 12px;
  }
  .card--front .brand__name { color: var(--grey); font-size: 48px; }
  .person {
    position: absolute; top: 96px; right: 36px; text-align: right;
  }
  .person__name { color: var(--green); font-size: 20px; font-weight: 600; letter-spacing: .5px; }
  .person__role { color: var(--grey); font-size: 12px; margin-top: 2px; letter-spacing: .5px; }
  .contact {
    position: absolute; top: 158px; left: 30px;
    list-style: none; font-size: 13px; color: var(--grey); letter-spacing: .8px;
  }
  .contact li { display: flex; align-items: center; gap: 9px; line-height: 18px; }
  .contact svg { width: 9px; height: 9px; fill: var(--green); flex: none; }
  .contact .accent { color: var(--green); }
  .wave { position: absolute; left: 0; bottom: 0; width: 500px; height: 150px; }
  .address {
    position: absolute; right: 30px; bottom: 30px;
    text-align: right; color: #fff; font-size: 12.5px; letter-spacing: 1px; line-height: 18px;
  }
</style>
</head>
<body>

  <section class="card card--back" aria-label="Business card, back">
    <div class="brand">
      <span class="brand__dot"></span>
      <span class="brand__name">brovix</span>
    </div>
    <p class="site">www.<span class="accent">brovix</span>.example</p>
  </section>

  <section class="card card--front" aria-label="Business card, front">
    <div class="brand">
      <span class="brand__dot"></span>
      <span class="brand__name">brovix</span>
    </div>

    <div class="person">
      <p class="person__name">Halyna Dorosh</p>
      <p class="person__role">Founder</p>
    </div>

    <ul class="contact">
      <li>
        <svg viewBox="0 0 10 10"><path d="M2 0h2l1 3-1.5 1a6 6 0 0 0 2.5 2.5L7 5l3 1v2c0 1-1 2-2 2A8 8 0 0 1 0 2c0-1 1-2 2-2z"/></svg>
        <span>780.555.0184</span>
      </li>
      <li>
        <svg viewBox="0 0 10 10"><path d="M0 2h10v6H0z M1 3l4 3 4-3" fill="none" stroke="#8cc63f" stroke-width="1.2"/></svg>
        <span>hello@brovix.example</span>
      </li>
      <li>
        <svg viewBox="0 0 10 10"><circle cx="5" cy="5" r="4.2" fill="none" stroke="#8cc63f" stroke-width="1.2"/><path d="M1 5h8M5 1c-2 2-2 6 0 8M5 1c2 2 2 6 0 8" fill="none" stroke="#8cc63f" stroke-width=".8"/></svg>
        <span>www.<span class="accent">brovix</span>.example</span>
      </li>
    </ul>

    <svg class="wave" viewBox="0 0 500 150" aria-hidden="true">
      <path d="M0 85 C 90 140, 200 125, 280 60 S 430 -5, 500 5 L500 150 L0 150 Z" fill="var(--grey-mid)"/>
      <path d="M0 115 C 100 160, 200 140, 290 80 S 440 15, 500 25 L500 150 L0 150 Z" fill="var(--green)"/>
    </svg>

    <p class="address">20517 87ave<br>T6K4N8 Edmonton, Alberta</p>
  </section>

</body>
</html>
```